QRV Advisors needs a web site

We need a web site for www.qrvadvisors-example.com. QRV is a mergers and acquisition consulting company that focuses our buyer and seller services on logistics companies. We help put companies together, and help with legal and financial due diligence. We want the web site to express our service and show the logistics components. We want personalized images versus pictures of trucks and airplanes.

Our new logo uses Burgandy and grey colors. Image attached. We are not in to bold, big letters...classy, artistic, low key preferred. Confidentiality, experience, professional are what we want to express on the site.

All we expect for the first part of this project is a home page, and one subpage.  We are budgeting other funds for the technical aspects of the web site

Reason: All that I'm seeing so far is trucks, forklifts and planes. We are a legal mergers and acquisitions firm that focus on logistics. I like some of the images to say logistics, but really want it say legal, financial, and putting companies together. Will pay extra for the sub page if someone can impress us with a home page.

Reason: Swamped with another project at the moment...will work on this over the weekend and provide designer feedback and select final design by Tuesday

```html
<!DOCTYPE html>
<html lang="en">
<head>
<meta charset="utf-8">
<title>QRV Advisors — Home</title>
<link href="https://fonts.googleapis.com/css2?family=Open+Sans:wght@300;400;600;700&display=swap" rel="stylesheet">
<style>
  :root {
    --burgundy: #9b0b36;
    --burgundy-dark: #7a0829;
    --ink: #444;
    --muted: #9a9a9a;
    --line: #a9a9a9;
    --footer: #4d4d4d;
    --page-top: #ffffff;
    --page-band: #e4e4e4;
    --page-bottom: #fbfbfb;
  }
  * { box-sizing: border-box; margin: 0; padding: 0; }
  html, body { width: 1200px; height: 883px; overflow: hidden; }
  body {
    font-family: "Open Sans", Arial, sans-serif;
    color: var(--ink);
    background: linear-gradient(var(--page-top) 0 118px, var(--page-band) 118px, var(--page-bottom) 520px, var(--page-bottom));
    position: relative;
  }

  .site-header { position: absolute; top: 0; left: 110px; width: 980px; height: 100px; }
  .brand {
    position: absolute; left: 8px; top: 26px;
    display: flex; align-items: center; gap: 14px;
    font-size: 40px; font-weight: 400; color: var(--burgundy); letter-spacing: 0.5px;
  }
  .brand-mark { width: 22px; height: 22px; background: var(--burgundy); }
  .contact { position: absolute; right: 0; top: 31px; text-align: right; font-size: 15px; color: #444; line-height: 24px; }
  .contact-row { display: flex; justify-content: flex-end; align-items: center; gap: 18px; }
  .contact-row svg { width: 15px; height: 15px; fill: #555; }

  .main-nav {
    position: absolute; top: 103px; left: 110px; width: 980px; height: 44px;
    background: linear-gradient(#a80d3c, var(--burgundy-dark));
    border-radius: 3px; display: flex;
  }
  .main-nav a {
    color: #fff; text-decoration: none; font-size: 14.5px;
    line-height: 44px; padding: 0 26px; border-right: 1px solid rgba(0,0,0,0.25);
    box-shadow: 1px 0 0 rgba(255,255,255,0.08);
  }
  .main-nav a.is-active { background: rgba(0,0,0,0.12); }
  .search { position: absolute; right: 6px; top: 11px; display: flex; gap: 5px; }
  .search-field {
    width: 179px; height: 23px; border-radius: 3px; background: #f2f2f2;
    font-size: 12px; color: #777; padding: 3px 10px; font-family: inherit;
  }
  .search-button { width: 42px; height: 23px; border-radius: 3px; background: #e8e8e8; display: flex; align-items: center; justify-content: center; }
  .search-button svg { width: 14px; height: 14px; }

  .hero {
    position: absolute; top: 158px; left: 110px; width: 980px; height: 332px;
    background: linear-gradient(#cdcbd2, #f3f3f5 55%, #fafafa);
    border-radius: 4px; overflow: hidden;
  }
  .hero-title { position: absolute; z-index: 2; left: 27px; top: 70px; font-size: 32px; font-weight: 400; color: #444; }
  .hero-title strong { color: var(--burgundy); font-weight: 700; }
  .hero-text {
    position: absolute; z-index: 2; left: 27px; top: 118px; width: 345px;
    font-size: 14px; line-height: 24px; font-weight: 300; color: #555; letter-spacing: -0.1px;
  }
  .button {
    position: absolute; z-index: 2; left: 26px; top: 211px; width: 94px; height: 31px;
    background: linear-gradient(#a80d3c, var(--burgundy-dark)); color: #fff;
    border-radius: 4px; font-size: 14.5px; text-align: center; line-height: 31px; text-decoration: none;
  }
  .hero-visual {
    position: absolute; left: 380px; top: 42px; width: 600px; height: 290px;
    background: linear-gradient(100deg, #c7ceda, #a9b6c9 45%, #d9d3cc 80%, #bfc8d6);
    border-radius: 6px 0 0 0;
  }

  .welcome {
    position: absolute; top: 506px; left: 110px; width: 980px; height: 135px;
    background: #fff; border-radius: 3px;
  }
  .welcome-visual {
    position: absolute; left: 17px; top: 11px; width: 178px; height: 113px;
    border-radius: 5px; background: linear-gradient(135deg, #2e3a4a, #6d7d90 60%, #3a4656);
  }
  .welcome-title { position: absolute; left: 218px; top: 4px; font-size: 24px; font-weight: 400; color: #444; }
  .welcome-title span { color: var(--burgundy); }
  .welcome-text {
    position: absolute; left: 218px; top: 46px; width: 745px;
    font-size: 12.5px; line-height: 24px; font-weight: 300; color: var(--muted); letter-spacing: -0.1px;
  }

  .services { position: absolute; top: 670px; left: 109px; display: flex; gap: 7px; }
  .service-card {
    width: 239px; height: 138px; border: 1px solid var(--line); border-radius: 4px;
    background: #fff; padding: 7px 9px 0 9px;
  }
  .service-card:nth-child(3) { margin-left: 2px; }
  .service-card:nth-child(4) { margin-left: 1px; }
  .service-title { font-size: 15px; font-weight: 400; color: #444; line-height: 20px; letter-spacing: -0.3px; }
  .service-visual { margin-top: 7px; width: 219px; height: 82px; border-radius: 4px; }
  .visual-meeting { background: linear-gradient(90deg, #8b8f98, #c9c4bd 50%, #7c8797); }
  .visual-planning { background: linear-gradient(90deg, #d6d8dc, #8a8f98 50%, #e1e3e6); }
  .visual-growth { background: linear-gradient(120deg, #0e3d5c, #1c5f86 60%, #2a79a6); }
  .visual-consult { background: linear-gradient(90deg, #6b7078, #9ea3aa 50%, #5f646c); }

  .site-footer {
    position: absolute; top: 840px; left: 110px; width: 980px; height: 43px;
    background: var(--footer); color: #fff; font-size: 13px; text-align: center; line-height: 43px;
  }
</style>
</head>
<body>
  <header class="site-header">
    <div class="brand"><span class="brand-mark"></span>QRV Advisors</div>
    <div class="contact">
      <div class="contact-row">
        <svg viewBox="0 0 16 16" aria-hidden="true"><path d="M3.5 1.5l2.5 0 1 3.5-1.7 1.2c.8 1.8 2.2 3.2 4 4L10.5 8.5l3.5 1v2.5c0 1-1 2-2 2C6.5 14 2 9.5 1.5 3.5c0-1 1-2 2-2z"/></svg>
        <span>555 014 2290</span>
      </div>
      <div class="contact-row">
        <svg viewBox="0 0 16 16" aria-hidden="true"><path d="M1 3h14v1.5L8 9 1 4.5z"/><path d="M1 6l7 4.5L15 6v7H1z"/></svg>
        <span>mara@qrvadvisors-example.com</span>
      </div>
    </div>
  </header>

  <nav class="main-nav">
    <a href="#" class="is-active">Home</a>
    <a href="#">About Us</a>
    <a href="#">Legal Help</a>
    <a href="#">Financial Help</a>
    <a href="#">Contact Us</a>
    <div class="search">
      <div class="search-field">Search...</div>
      <div class="search-button">
        <svg viewBox="0 0 16 16" aria-hidden="true"><circle cx="6.5" cy="6.5" r="4.5" fill="none" stroke="#888" stroke-width="2"/><line x1="10" y1="10" x2="14" y2="14" stroke="#888" stroke-width="2.2"/></svg>
      </div>
    </div>
  </nav>

  <section class="hero">
    <div class="hero-visual" role="img" aria-label="Photo of a globe with parcels, a plane, delivery vans and a truck beside three smiling business people at a laptop"></div>
    <h1 class="hero-title"><strong>QRV</strong> Advisors</h1>
    <p class="hero-text">Lorem ipsum dolor sit amet, consectetuer adipiscing elit, sed diam nonummy nibh euismod tincidunt ut laoreet dolore magna aliquam erat volutpat.</p>
    <a href="#" class="button">Read More</a>
  </section>

  <section class="welcome">
    <div class="welcome-visual" role="img" aria-label="Photo of a businessman touching a transparent logistics interface"></div>
    <h2 class="welcome-title">Welcome To <span>Quarry Ridge Ventures</span></h2>
    <p class="welcome-text">QRV assists business owners within the logistics industry to implement growth and exit strategies. We offer business planning and merger and acquisition(M&amp;A) advisory services. QRV services are offered by industry executives with extensive M&amp;A experience. Your company will benefit from a unique and outside perspective from consultants that understand your business.</p>
  </section>

  <section class="services">
    <article class="service-card">
      <h3 class="service-title">M&amp;A Advisory Services</h3>
      <div class="service-visual visual-meeting" role="img" aria-label="Photo of business people shaking hands across a meeting table"></div>
    </article>
    <article class="service-card">
      <h3 class="service-title">Business Planning</h3>
      <div class="service-visual visual-planning" role="img" aria-label="Photo collage of a businessman with a rising chart and a handshake"></div>
    </article>
    <article class="service-card">
      <h3 class="service-title">Your Growth Strategy</h3>
      <div class="service-visual visual-growth" role="img" aria-label="Photo of a hand drawing a rising bar chart with an arrow"></div>
    </article>
    <article class="service-card">
      <h3 class="service-title">Logistics Consultancy</h3>
      <div class="service-visual visual-consult" role="img" aria-label="Photo of two small figures pushing puzzle pieces together"></div>
    </article>
  </section>

  <footer class="site-footer">Copyright 2014. QRV ADVISORS. All rights reserved.</footer>
</body>
</html>
```